Product Designer Business Card

Small product design, engineering and prototyping firm in need of a clean, professional business card design. To support our 3D design and drawing services, we offer 3D printing, molding, and casting of plastics, silicones, resins, etc. Our logo can still be modified/changed if necessary. The red/orange color is preferred, but may be substituted with blue or green, potentially. Either way, the colour of the logo should be match/compliment colors used throughout the design. One thought is to have the logo/contact info on one side, with the other side describing services offered, like with a small icon of 3D printer, molding, casting, and computer with a 3D model on-screen.
Industry/Entity Type
Mechanical Engineering
Contact Information for Business Card
Company: Kelvar Design
Phone: 613-582-9047
Email: mark@kelvardesign.ca

```html
<!DOCTYPE html>
<html lang="en">
<head>
<meta charset="utf-8">
<title>Kelvar Design – Business Card</title>
<link rel="stylesheet" href="https://fonts.googleapis.com/css2?family=Exo+2:wght@500;600&family=Open+Sans:wght@400&display=swap">
<style>
  :root {
    --stage: #2b2b2d;
    --card-white: #ffffff;
    --brand-red: #c8140c;
    --brand-dark: #7a0f08;
    --ink: #3a3a3a;
    --ink-soft: #555555;
    --rule: #9a9a9a;
    --back-top: #85150b;
    --back-bottom: #ea2a0c;
    --on-red: #ffffff;
  }
  * { box-sizing: border-box; margin: 0; padding: 0; }
  html, body { width: 1200px; height: 1108px; overflow: hidden; }
  body {
    background: var(--stage);
    display: flex;
    align-items: center;
    justify-content: center;
    gap: 60px;
    font-family: "Open Sans", sans-serif;
  }
  .card {
    width: 420px;
    height: 700px;
    border-radius: 24px;
    position: relative;
    overflow: hidden;
  }
  /* Front */
  .card-front {
    background: var(--card-white);
    display: flex;
    flex-direction: column;
    align-items: center;
    padding-top: 110px;
  }
  .brand-lockup {
    display: flex;
    align-items: center;
    gap: 16px;
  }
  .brand-dot {
    flex: none;
    width: 30px; height: 30px;
    border-radius: 50%;
    background: var(--brand-red);
  }
  .brand-name {
    font-family: "Exo 2", sans-serif;
    font-weight: 600;
    font-size: 40px;
    line-height: 48px;
    letter-spacing: 7px;
    color: var(--brand-red);
  }
  .brand-name-stack { display: flex; flex-direction: column; }
  .person { margin-top: 150px; text-align: center; }
  .person-name {
    font-family: "Exo 2", sans-serif;
    font-weight: 600;
    font-size: 30px;
    color: var(--brand-red);
    letter-spacing: 0.5px;
  }
  .person-title {
    font-family: "Exo 2", sans-serif;
    font-weight: 500;
    font-size: 20px;
    color: var(--ink-soft);
    margin-top: 2px;
  }
  .contact-divider {
    display: flex; align-items: center; gap: 8px;
    width: 300px; margin-top: 22px;
  }
  .contact-divider .rule { flex: 1; height: 1px; background: var(--rule); }
  .contact-icon {
    width: 28px; height: 28px; border-radius: 4px;
    background: var(--brand-red);
    display: flex; align-items: center; justify-content: center;
  }
  .contact-list { margin-top: 18px; text-align: center; font-size: 21px; line-height: 31px; color: var(--ink); }
  .contact-list .accent { color: var(--brand-red); }
  /* Back */
  .card-back {
    background: linear-gradient(180deg, var(--back-top) 0%, #b41a0b 45%, var(--back-bottom) 100%);
  }
  .back-brand {
    position: absolute; right: 48px; top: 430px;
    display: flex; align-items: center; gap: 12px;
  }
  .back-brand .brand-dot { background: var(--on-red); width: 30px; height: 30px; }
  .back-brand .brand-name { color: var(--on-red); font-size: 42px; }
  .services {
    position: absolute; left: 24px; right: 24px; top: 540px;
    display: flex; justify-content: space-between;
  }
  .service { display: flex; flex-direction: column; align-items: center; width: 88px; }
  .service-icon {
    width: 74px; height: 74px;
    border: 2px solid rgba(255,255,255,0.85);
    border-radius: 8px;
    display: flex; align-items: center; justify-content: center;
  }
  .service-label {
    margin-top: 10px;
    font-family: "Exo 2", sans-serif;
    font-weight: 500;
    font-size: 19px;
    color: var(--on-red);
    white-space: nowrap;
  }
</style>
</head>
<body>

  <section class="card card-front">
    <div class="brand-lockup">
      <span class="brand-dot"></span>
      <span class="brand-name brand-name-stack">
        <span>Kelvar</span>
        <span>Design</span>
      </span>
    </div>

    <div class="person">
      <div class="person-name">DANIEL FRASER</div>
      <div class="person-title">Managing Director</div>
    </div>

    <div class="contact-divider">
      <span class="rule"></span>
      <span class="contact-icon" aria-label="Phone">
        <svg width="18" height="18" viewBox="0 0 24 24"><path fill="#fff" d="M6.6 10.8a15 15 0 0 0 6.6 6.6l2.2-2.2c.3-.3.7-.4 1-.2 1.1.4 2.3.6 3.6.6.6 0 1 .4 1 1V20c0 .6-.4 1-1 1A17 17 0 0 1 3 4c0-.6.4-1 1-1h3.5c.6 0 1 .4 1 1 0 1.3.2 2.5.6 3.6.1.3 0 .7-.2 1z"/></svg>
      </span>
      <span class="contact-icon" aria-label="Email">
        <svg width="18" height="18" viewBox="0 0 24 24"><rect x="3" y="6" width="18" height="12" fill="none" stroke="#fff" stroke-width="2"/><path d="M3 6l9 7 9-7" fill="none" stroke="#fff" stroke-width="2"/></svg>
      </span>
      <span class="contact-icon" aria-label="Website">
        <svg width="18" height="18" viewBox="0 0 24 24"><circle cx="12" cy="12" r="8.5" fill="none" stroke="#fff" stroke-width="2"/><path d="M3.5 12h17M12 3.5c3 3 3 14 0 17M12 3.5c-3 3-3 14 0 17" fill="none" stroke="#fff" stroke-width="1.5"/></svg>
      </span>
      <span class="rule"></span>
    </div>

    <div class="contact-list">
      <div>613-582-9047</div>
      <div>mark@kelvardesign.ca</div>
      <div>www.<span class="accent">kelvardesign</span>.ca</div>
    </div>
  </section>

  <section class="card card-back">
    <div class="back-brand">
      <span class="brand-dot"></span>
      <span class="brand-name">Kelvar</span>
    </div>

    <div class="services">
      <div class="service">
        <div class="service-icon">
          <svg width="44" height="44" viewBox="0 0 44 44" fill="none" stroke="#fff" stroke-width="2.5">
            <rect x="5" y="5" width="34" height="34" rx="2"/>
            <path d="M5 13h34"/><rect x="15" y="18" width="14" height="5" fill="#fff"/>
            <path d="M22 23v6"/><rect x="13" y="30" width="18" height="5"/>
          </svg>
        </div>
        <div class="service-label">3D Printer</div>
      </div>
      <div class="service">
        <div class="service-icon">
          <svg width="44" height="44" viewBox="0 0 44 44" fill="none" stroke="#fff" stroke-width="2.5">
            <rect x="14" y="4" width="16" height="6" fill="#fff"/><path d="M22 10v8"/>
            <rect x="10" y="18" width="24" height="6"/><rect x="8" y="28" width="28" height="10"/>
            <path d="M16 28v4h12v-4"/>
          </svg>
        </div>
        <div class="service-label">Molding</div>
      </div>
      <div class="service">
        <div class="service-icon">
          <svg width="44" height="44" viewBox="0 0 44 44" fill="none" stroke="#fff" stroke-width="2.5">
            <path d="M8 8l12 6-4 6-10-4z" fill="#fff"/><path d="M18 20c2 6 2 10 2 14"/>
            <path d="M14 38h22M22 38c0-6 4-10 8-10s4 6 4 10"/>
          </svg>
        </div>
        <div class="service-label">Casting</div>
      </div>
      <div class="service">
        <div class="service-icon">
          <svg width="44" height="44" viewBox="0 0 44 44" fill="none" stroke="#fff" stroke-width="2.5">
            <rect x="5" y="6" width="34" height="24" rx="2"/><path d="M18 30v6M26 30v6M13 37h18"/>
            <path d="M22 11l7 4v7l-7 4-7-4v-7zM15 15l7 4 7-4M22 19v7"/>
          </svg>
        </div>
        <div class="service-label">3d Model</div>
      </div>
    </div>
  </section>

</body>
</html>
```